Payment company requires web design

We need a web design for a new company based in Singapore.

The company focuses on providing 2 key products: 1) an alternative payment option (i.e. like quib or trelloquin options) on the traditional checkout process 2) a replacement/outsource of a merchants payment page. Key in the UX flow is a end customer dashboard that manages all payments.

We look to provide a simple, fluid and easy to use payment process. The dashboard is minimalistic that allows easy navigation, review of transactions and all available options through gamification.

The final design should communicate ease of use, flexibility and transparency.

Target Market(s)

The value is for the merchant - retail/travel/insurance companies. However its the merchant's end customers that are the target and who the UX is built for.

Industry/Entity Type

It Company

Logo Text

zelnar

Number of Pages Required

5+ page

Colors
ec1f27

Requirements
Must have
• 7 pages mimicking UX flow
• payment page * 2 - 1) alternative payment type 2) outsource of merchants payment page to our business
• our landing page
• end customer verification page
• end customer registration
• customer dashboard
• UX flow in attached file
Nice to have
• open to ideas
• have asked for the logo to be added
• logo to have the colour red (chinese for prosperity)
• the company is all about flexibility, transparency in personal finance management with the option of instalment payments

```html
<!DOCTYPE html>
<html lang="en">
<head>
<meta charset="utf-8">
<title>Zelnar</title>
<link href="https://fonts.googleapis.com/css2?family=Open+Sans:wght@400;600;700&display=swap" rel="stylesheet">
<style>
:root{
  --red:#ec1f27;
  --ink:#222;
  --text:#666;
  --muted:#999;
  --line:#ddd;
  --band:#f4f4f4;
  --dark:#1f1f1f;
}
*{margin:0;padding:0;box-sizing:border-box}
html,body{width:773px;height:1200px;overflow:hidden;background:#fff;font-family:'Open Sans',Arial,sans-serif;color:var(--text)}
.page{position:relative;width:773px;height:1200px}
.abs{position:absolute}

.brand{left:86px;top:16px;display:flex;align-items:center;gap:7px}
.brand-mark{width:16px;height:16px;border-radius:50%;background:var(--red)}
.brand-name{font-size:27px;font-weight:700;color:var(--red);letter-spacing:-.3px;line-height:1}
.nav{right:86px;top:26px;display:flex;gap:19px;font-size:7.5px;color:#555;align-items:center}
.nav .active{color:var(--red)}

.hero{left:0;top:64px;width:773px;height:258px;background:linear-gradient(90deg,#5a2a22 0%,#8a3a2c 30%,#b58a80 55%,#6a5a6a 80%,#3a2a2e 100%)}
.hero-title{left:86px;top:140px;font-size:15px;font-weight:700;color:#fff;line-height:19px}
.hero-btn{left:86px;top:185px;width:77px;height:26px;border:1px solid #fff;color:#fff;font-size:7px;display:flex;align-items:center;justify-content:center}
.arrow{top:183px}

.intro-title{left:0;width:773px;top:368px;text-align:center;font-size:16px;color:var(--red)}
.intro-text{left:86px;width:601px;top:392px;text-align:center;font-size:7.3px;line-height:13.4px}

.feature{top:479px;width:190px;text-align:center}
.feature .ring{width:63px;height:63px;margin:0 auto;border:1px solid #999;border-radius:50%;display:flex;align-items:center;justify-content:center}
.feature .ring span{width:53px;height:53px;border-radius:50%;background:#f1f1f1;display:flex;align-items:center;justify-content:center}
.feature h3{font-size:12.5px;font-weight:400;color:var(--ink);margin-top:10px}
.feature p{font-size:6.2px;line-height:9.4px;margin-top:5px;color:var(--muted)}

.devices{left:72px;top:672px;width:340px;height:232px;border-radius:10px;background:linear-gradient(135deg,#eef2f7 0%,#dfe6ef 60%,#c9d3df 100%)}
.app-title{left:434px;top:700px;font-size:12px;color:var(--ink);line-height:16px}
.app-text{left:434px;top:742px;width:253px;font-size:6.6px;line-height:11.4px;text-align:justify}
.dl-label{left:434px;top:840px;font-size:6.5px;color:var(--ink)}
.store{top:855px;width:99px;height:32px;display:flex;align-items:center;gap:7px;padding-left:12px;font-size:6px;line-height:8px}
.store b{font-weight:600;font-size:6.5px}
.store.dark{left:434px;background:var(--dark);color:#fff}
.store.light{left:543px;border:1px solid #ccc;color:#333}
.store i{width:14px;height:14px;border-radius:50%;display:block}
.store.dark i{background:#fff}
.store.light i{background:var(--red)}

.faq{left:0;top:981px;width:773px;height:155px;background:var(--band)}
.faq h2{position:absolute;top:27px;width:773px;text-align:center;font-size:12px;font-weight:400;color:var(--ink)}
.faq h3{position:absolute;top:53px;width:773px;text-align:center;font-size:11.3px;font-weight:400;color:var(--ink)}
.faq p{position:absolute;left:88px;width:597px;top:74px;text-align:center;font-size:6.4px;line-height:11.2px}
.dots{position:absolute;top:120px;left:359px;display:flex;gap:10px}
.dots span{width:5px;height:5px;border-radius:50%;background:#ccc}
.dots span:first-child{background:#777}

.foot-links{left:86px;top:1154px;font-size:6.8px;color:#777;word-spacing:2px}
.copy{left:86px;top:1172px;font-size:6.5px;color:#888}
.social{top:1160px;width:16px;height:16px;border-radius:50%}
</style>
</head>
<body>
<div class="page">

  <header>
    <div class="abs brand"><span class="brand-mark"></span><span class="brand-name">Zelnar</span></div>
    <nav class="abs nav">
      <span class="active">Home</span><span>About</span><span>Services</span><span>FAQs</span><span>Contact Us</span>
      <svg width="7" height="7" viewBox="0 0 10 10"><circle cx="4" cy="4" r="3" fill="none" stroke="#222" stroke-width="1.6"/><line x1="6.2" y1="6.2" x2="9" y2="9" stroke="#222" stroke-width="1.8"/></svg>
    </nav>
  </header>

  <section>
    <div class="abs hero" role="img" aria-label="Hand holding a payment card against a blurred shop background"></div>
    <div class="abs hero-title">Morbi accumsan<br>sapien euismod consectetur</div>
    <div class="abs hero-btn">Get Started Now</div>
    <svg class="abs arrow" style="left:15px" width="12" height="20" viewBox="0 0 12 20"><polyline points="10,2 2,10 10,18" fill="none" stroke="#ddd" stroke-width="2.5"/></svg>
    <svg class="abs arrow" style="left:746px" width="12" height="20" viewBox="0 0 12 20"><polyline points="2,2 10,10 2,18" fill="none" stroke="#ddd" stroke-width="2.5"/></svg>
  </section>

  <section>
    <h1 class="abs intro-title" style="font-weight:400">Morbi accumsan, sapien ut euismod consectetur</h1>
    <p class="abs intro-text">Aenean varius sed enim non porttitor. Nunc tincidunt sem at hendrerit convallis. Morbi rutrum libero sem. Vestibulum a venenatis lacus. In elit sapien, efficitur nec suscipit ut, egestas sed mauris. Sed aliquet nisi ut mauris malesuada, ut luctus nisl sagittis. Mauris vulputate maximus velit, quis volutpat augue dictum vel. Praesent lacinia, libero id semper vulputate, purus urna pellentesque justo, quis fringilla velit risus non ligula. Donec interdum nisl id elit ultrices, eget cursus erat viverra. Etiam tincidunt elit lorem, quis semper elit convallis a. Proin mollis sem eget elit consectetur feugiat id non risus. Phasellus sed mauris quam.</p>

    <div class="abs feature" style="left:83px">
      <div class="ring"><span>
        <svg width="30" height="26" viewBox="0 0 30 26" fill="none" stroke="#ec1f27" stroke-width="1.3"><rect x="1" y="4" width="28" height="21"/><line x1="1" y1="9" x2="29" y2="9"/><line x1="8" y1="1" x2="8" y2="6"/><line x1="22" y1="1" x2="22" y2="6"/><line x1="5" y1="14" x2="25" y2="14"/><line x1="5" y1="19" x2="25" y2="19"/><line x1="10" y1="11" x2="10" y2="23"/><line x1="15" y1="11" x2="15" y2="23"/><line x1="20" y1="11" x2="20" y2="23"/></svg>
      </span></div>
      <h3>Installment Payments</h3>
      <p>Aliquam ut risus enim. Nunc sit amet tellus neque. Phasellus sit amet nibh sodales, vehicula augue et, iaculis dolor. Duis fringilla urna vitae sem euismod vestibulum.</p>
    </div>
    <div class="abs feature" style="left:291px">
      <div class="ring"><span>
        <svg width="32" height="26" viewBox="0 0 32 26" fill="none" stroke="#ec1f27" stroke-width="1.3"><circle cx="11" cy="15" r="7" stroke-dasharray="3 1.5" stroke-width="3"/><circle cx="11" cy="15" r="3"/><circle cx="23" cy="8" r="5" stroke-dasharray="2.5 1.3" stroke-width="2.6"/><circle cx="23" cy="8" r="2"/></svg>
      </span></div>
      <h3>Easy &amp; Transparent Processing</h3>
      <p>Aliquam ut risus enim. Nunc sit amet tellus neque. Phasellus sit amet nibh sodales, vehicula augue et, iaculis dolor. Duis fringilla urna vitae sem euismod vestibulum.</p>
    </div>
    <div class="abs feature" style="left:500px">
      <div class="ring"><span>
        <svg width="26" height="28" viewBox="0 0 26 28" fill="none" stroke="#ec1f27" stroke-width="1.3"><path d="M6 12V8a7 7 0 0 1 14 0v4"/><rect x="2" y="12" width="22" height="15"/><line x1="2" y1="18" x2="24" y2="18"/><line x1="2" y1="22" x2="24" y2="22"/><line x1="6" y1="22" x2="10" y2="18"/><line x1="12" y1="22" x2="16" y2="18"/><line x1="18" y1="22" x2="22" y2="18"/></svg>
      </span></div>
      <h3>Secured Details</h3>
      <p>Aliquam ut risus enim. Nunc sit amet tellus neque. Phasellus sit amet nibh sodales, vehicula augue et, iaculis dolor. Duis fringilla urna vitae sem euismod vestibulum.</p>
    </div>
  </section>

  <section>
    <div class="abs devices" role="img" aria-label="Laptop and phone showing the customer payment dashboard"></div>
    <h2 class="abs app-title" style="font-weight:400">Aenean varius sed enim non porttitor.<br>Nunc tincidunt sem at hendrerit convallis.</h2>
    <p class="abs app-text">Morbi accumsan, sapien ut euismod consectetur, justo nibh egestas diam, a tempus quam enim tempus arcu. Pellentesque nec bibendum orci. Vestibulum id maximus sem. In hac habitasse platea dictumst. Fusce molestie nisl ac turpis vestibulum porta. Praesent non eros in tellus placerat varius. Phasellus ut sodales mauris, vitae dignissim tortor. Aliquam ut risus enim. Nunc sit amet tellus neque. Phasellus sit amet nibh sodales, vehicula augue et, iaculis dolor. Duis fringilla urna vitae sem euismod vestibulum.</p>
    <div class="abs dl-label">Download from here</div>
    <div class="abs store dark"><i></i><span>Download it from<br><b>APP DEPOT</b></span></div>
    <div class="abs store light"><i></i><span>Download it from<br><b>PLAY BAZAAR</b></span></div>
  </section>

  <section class="abs faq">
    <h2>FAQs</h2>
    <h3>Morbi accumsan, sapien ut euismod consectetur, justo nibh egestas diam?</h3>
    <p>Nunc tincidunt sem at hendrerit convallis. Morbi rutrum libero sem. Vestibulum a venenatis lacus. In elit sapien, efficitur nec suscipit ut, egestas sed mauris. Sed aliquet nisi ut mauris malesuada, ut luctus nisl sagittis. Mauris vulputate maximus velit, quis volutpat augue dictum vel. Praesent lacinia, libero id semper vulputate, purus urna pellentesque justo, quis fringilla velit risus non ligula. Donec interdum nisl id elit ultrices, eget cursus erat viverra.</p>
    <div class="dots"><span></span><span></span><span></span><span></span></div>
  </section>

  <footer>
    <div class="abs foot-links">Home &nbsp;| &nbsp;About &nbsp;| &nbsp;Services &nbsp;| &nbsp;FAQs &nbsp;| &nbsp;Contact Us</div>
    <div class="abs copy">Copyright © 2016 &nbsp;Company name. &nbsp;All rights reserved.</div>
    <span class="abs social" style="left:650px;background:#3b5998"></span>
    <span class="abs social" style="left:671px;background:#1da1f2"></span>
  </footer>

</div>
</body>
</html>
```